Unique Business Card Design

Unique Business Card design for our orthotic and prosthetic company. Our logo is on our website, color is light blue. Unique shape (artificial leg shaped, vertical, etc..) preferred. Logo, business name, individual name and basic demographics needed.

Industry/Entity Type

Business

Contact Information for Business Card

Logo, Industry, Phone # Logo, "Prosthetic & Orthotic Services" Place to add individual name and contact info

Colors
cee9f5

Requirements
Must have
• The icon must be there, placement of "Prosthetic & Orthotic Services" can be moved
Nice to have
• Like the mix of light blue, and a little darker blue. One design included the icons from my website which was a nice touch

```html
<!DOCTYPE html>
<html lang="en">
<head>
<meta charset="utf-8">
<title>Limbworks Inc. Business Card</title>
<link href="https://fonts.googleapis.com/css2?family=Open+Sans:wght@400;600;700&family=Crimson+Text:ital@1&display=swap" rel="stylesheet">
<style>
  :root {
    --page-bg: #e9edf0;
    --card-bg: #f3f7fa;
    --card-edge: #d7e1e8;
    --brand-blue: #1f4a8c;
    --light-blue: #cee9f5;
    --ink: #262b35;
  }
  * { margin: 0; padding: 0; box-sizing: border-box; }
  html, body { width: 1200px; height: 969px; overflow: hidden; }
  body {
    background: var(--page-bg);
    font-family: "Open Sans", Arial, sans-serif;
    position: relative;
  }
  .card {
    position: absolute;
    left: 100px; top: 200px;
    width: 1000px; height: 568px;
    background: linear-gradient(160deg, var(--card-bg), var(--light-blue));
    border: 1px solid var(--card-edge);
    border-radius: 30px;
    overflow: hidden;
    box-shadow: 0 12px 40px rgba(30, 50, 80, 0.15);
  }
  .side-band {
    position: absolute;
    left: 0; top: 0;
    width: 112px; height: 100%;
    background: var(--brand-blue);
  }
  .brand-mark {
    position: absolute;
    left: 36px; top: 45px;
    width: 144px; height: 144px;
    border-radius: 50%;
    background: var(--card-bg);
    border: 6px solid var(--brand-blue);
  }
  .brand-name {
    position: absolute;
    left: 215px; top: 66px;
    font-size: 38px;
    font-weight: 700;
    color: var(--brand-blue);
    letter-spacing: 0.5px;
  }
  .brand-rule {
    position: absolute;
    left: 215px; top: 122px;
    width: 362px; height: 2px;
    background: var(--brand-blue);
  }
  .tagline {
    position: absolute;
    left: 232px; top: 126px;
    font-family: "Crimson Text", Georgia, serif;
    font-style: italic;
    font-size: 23px;
    color: var(--brand-blue);
  }
  .person-name {
    position: absolute;
    left: 215px; top: 180px;
    font-size: 34px;
    font-weight: 700;
    color: var(--brand-blue);
    letter-spacing: 0.5px;
  }
  .person-title {
    position: absolute;
    left: 215px; top: 222px;
    font-size: 23px;
    font-weight: 600;
    color: var(--brand-blue);
  }
  .contact-list {
    position: absolute;
    right: 50px; top: 292px;
    list-style: none;
    text-align: right;
  }
  .contact-item {
    display: flex;
    justify-content: flex-end;
    align-items: center;
    gap: 14px;
    height: 38px;
    font-size: 23px;
    color: var(--ink);
  }
  .contact-icon { width: 26px; height: 26px; fill: var(--brand-blue); }
  .address {
    position: absolute;
    right: 45px; top: 492px;
    font-size: 24px;
    color: var(--ink);
  }
</style>
</head>
<body>
  <div class="card">
    <div class="side-band"></div>
    <div class="brand-mark"></div>
    <div class="brand-name">LIMBWORKS INC.</div>
    <div class="brand-rule"></div>
    <div class="tagline">Prosthetic &amp; Orthotic Services</div>
    <div class="person-name">MARLO VENKESH</div>
    <div class="person-title">CO LPO</div>

    <ul class="contact-list">
      <li class="contact-item">555.214.3080
        <svg class="contact-icon" viewBox="0 0 24 24" aria-hidden="true"><path d="M3 8c0-2 3-4 9-4s9 2 9 4v2h-5V8H8v2H3z"/><path d="M6 12h12l2 8H4z"/></svg>
      </li>
      <li class="contact-item">555.214.6742
        <svg class="contact-icon" viewBox="0 0 24 24" aria-hidden="true"><path d="M7 2h10a1 1 0 0 1 1 1v18a1 1 0 0 1-1 1H7a1 1 0 0 1-1-1V3a1 1 0 0 1 1-1zm1 3v12h8V5zm4 13.5a1 1 0 1 0 0 2 1 1 0 0 0 0-2z"/></svg>
      </li>
      <li class="contact-item">555-7031186
        <svg class="contact-icon" viewBox="0 0 24 24" aria-hidden="true"><path d="M7 3h10v5H7z"/><path d="M3 10h18v8h-3v-3H6v3H3z"/><path d="M7 16h10v5H7z"/></svg>
      </li>
      <li class="contact-item">mvenkesh@limbworksinc.com
        <svg class="contact-icon" viewBox="0 0 24 24" aria-hidden="true"><path d="M2 5h20v2l-10 6L2 7z"/><path d="M2 9l10 6 10-6v10H2z"/></svg>
      </li>
      <li class="contact-item">www.limbworksinc.com
        <svg class="contact-icon" viewBox="0 0 24 24" aria-hidden="true"><circle cx="12" cy="12" r="10"/><path d="M2 12h20M12 2c3 3 3 17 0 20M12 2c-3 3-3 17 0 20" stroke="#f3f7fa" stroke-width="1.6" fill="none"/></svg>
      </li>
    </ul>

    <div class="address">2380 W. 14th St., Fairbrook, NY 10990</div>
  </div>
</body>
</html>
```